Velvet Riot Rising Line of Sparkling Wine & Spirits

Back info: Nora Beth Quill Owner 555-318-4402 1480 E. Harlow Ave, Bldg. 2, & 3, Lodi Ca. 95871
Sparkling Wines & Memorabilia www.velvetriotrising.com
Ok I have uploaded the winning design. The color that I am after is the Fushia, Raspberry, Red, Matte Satin Matalic Finish. With a 24 Karet Gold color Foil. The Bottle is on the top row and it's the 2nd Bottle in. That is the Color that I want. This is the style of font. Make sure that you put what we're advertising. Good Luck to you all. Warmest regards, Nora
21 & up UniSex
Sparkling Wine and Memorabilia
there listed up above.....

```html
<!DOCTYPE html>
<html lang="en">
<head>
<meta charset="utf-8">
<title>Velvet Riot Rising – Business Card</title>
<link rel="stylesheet" href="https://fonts.googleapis.com/css2?family=Arimo:wght@400;700&display=swap">
<style>
  :root {
    --backdrop: #e6e6e6;
    --card: #ffffff;
    --raspberry: #d0157c;
    --raspberry-deep: #b80f6b;
    --gold: #e9b04c;
    --ink: #555555;
    --logo-ink: #3b3b3b;
    --rule: #c9c9c9;
  }
  * { margin: 0; padding: 0; box-sizing: border-box; }
  html, body { width: 1200px; height: 1200px; overflow: hidden; }
  body {
    background: var(--backdrop);
    font-family: "Arimo", Arial, sans-serif;
    position: relative;
  }
  .card {
    position: absolute;
    width: 688px;
    height: 393px;
    background: var(--card);
    box-shadow: 0 2px 6px rgba(0,0,0,0.12);
  }
  .card--front { left: 267px; top: 159px; }
  .card--back { left: 262px; top: 653px; }

  /* front */
  .holder {
    position: absolute;
    left: 188px;
    top: 148px;
    font-size: 27px;
    font-weight: 700;
    color: var(--raspberry);
    letter-spacing: 0.3px;
    white-space: nowrap;
  }
  .holder .slash { font-weight: 400; margin: 0 8px; }
  .holder .role { font-size: 18px; font-weight: 400; color: var(--gold); }
  .address {
    position: absolute;
    right: 372px;
    top: 201px;
    text-align: right;
    font-size: 16px;
    line-height: 21px;
    color: var(--ink);
    white-space: nowrap;
  }
  .divider {
    position: absolute;
    left: 345px;
    top: 203px;
    width: 1px;
    height: 40px;
    background: #777;
  }
  .contact {
    position: absolute;
    left: 360px;
    top: 201px;
    font-size: 16px;
    line-height: 21px;
    color: var(--ink);
    list-style: none;
    white-space: nowrap;
  }
  .contact li { display: flex; align-items: center; gap: 11px; }
  .contact svg { width: 14px; height: 14px; flex: none; }

  /* back */
  .bottle-art {
    position: absolute;
    left: 92px;
    top: 69px;
    width: 81px;
    height: 262px;
    border-radius: 6px;
    background: linear-gradient(to right, var(--raspberry-deep), #e0238c 50%, var(--raspberry-deep));
  }
  .brand-name {
    position: absolute;
    left: 192px;
    top: 170px;
    font-size: 41px;
    font-weight: 700;
    color: var(--logo-ink);
    letter-spacing: 0.5px;
    white-space: nowrap;
  }
  .brand-rule {
    position: absolute;
    left: 183px;
    top: 228px;
    width: 440px;
    height: 1px;
    background: linear-gradient(to right, var(--rule), var(--rule) 70%, rgba(201,201,201,0));
  }
  .tagline {
    position: absolute;
    left: 192px;
    top: 236px;
    font-size: 17px;
    letter-spacing: 2.4px;
    color: #333;
    white-space: nowrap;
  }
  .tagline strong { color: var(--raspberry); font-weight: 700; }
</style>
</head>
<body>
  <section class="card card--front">
    <h1 class="holder">NORA BETH QUILL<span class="slash">/</span><span class="role">Owner</span></h1>
    <p class="address">E. Harlow Ave<br>Bldg. 2, &amp; 3, Lodi Ca. 95871</p>
    <span class="divider"></span>
    <ul class="contact">
      <li>
        <svg viewBox="0 0 24 24" aria-hidden="true"><path fill="var(--raspberry)" d="M6.6 10.8a15.5 15.5 0 0 0 6.6 6.6l2.2-2.2a1 1 0 0 1 1-.25 11.4 11.4 0 0 0 3.6.57 1 1 0 0 1 1 1V20a1 1 0 0 1-1 1A17 17 0 0 1 3 4a1 1 0 0 1 1-1h3.5a1 1 0 0 1 1 1c0 1.25.2 2.45.57 3.57a1 1 0 0 1-.25 1z"/></svg>
        555-318-4402 1480
      </li>
      <li>
        <svg viewBox="0 0 24 24" aria-hidden="true"><circle cx="12" cy="12" r="11" fill="var(--raspberry)"/><path fill="#fff" d="M7 6c2 1 3 3 2 5s-3 1-3 4c2 1 3 3 3 5-3-1-6-4-6-8 0-2 1-4 4-6zm9 6c2 0 3 2 2 4s-3 3-4 1 0-5 2-5z"/></svg>
        www.velvetriotrising.com
      </li>
    </ul>
  </section>

  <section class="card card--back">
    <div class="bottle-art" role="img" aria-label="Product illustration: raspberry pink sparkling wine bottle with gold foil"></div>
    <p class="brand-name">Velvet Riot Rising</p>
    <span class="brand-rule"></span>
    <p class="tagline">SPARKLING <strong>WINES &amp; MEMORABILIA</strong></p>
  </section>
</body>
</html>
```